Family business needs stationery redesign with new logo

Family owned company, established in 1987 wanting a brand 'refresh'. We are an electrical, refrigeration and construction company based in the Barkly Region Northern Territory, Australia. We have a new logo we would like to use which is uploaded along with our current letterhead and email signature. We are also dropping the word 'contractors' so please do not include this on any designs. Please note also, the 'orange' color used in our logo and designs should be Northern Territory red ochre which is as follows:

RGB (Hex): #C75B12
PantoneĀ® 159 C
CMYK: 1 / 74 / 100 / 7

We are needing our stationery redesigned using our new logo. Please include letterheads, business cards, envelopes, and email signatures.

We currently use our business letterheads for quotations, invoices, letters, HR matters, and internal memos.

We also need a separate simplified letterhead for internal paperwork such as employee leave forms, meeting agendas, and meeting minutes etc.

Reason: Needing more submissions of full package designs. We are wanting all our stationery, including business cards, letterheads, email signatures, envelopes, etc to be cohesive. We also require ALL the information, as supplied on our template letterhead, to be included on the new letterhead designs. including electrical license no.etc Thank you, R&W

Reason: needing more time as work has got in the way of looking over designs. A lot of designs not meeting the brief/criteria.

Industry/Entity Type

Business

Colors
0355a3
f37122

Requirements
Must have
• The 'orange' color used in the designs should be Northern Territory red ochre which is as follows:
• RGB (Hex): #C75B12
• PantoneĀ® 159 C
• CMYK: 1 / 74 / 100 / 7
• ***MUST INCLUDE ALL INFORMATION THAT IS ON OUR CURRENT LETTERHEAD***
Should not have
• Please do not include the word 'contractors'

```html
<!DOCTYPE html>
<html lang="en">
<head>
<meta charset="utf-8">
<title>R&amp;W Business Card</title>
<link href="https://fonts.googleapis.com/css2?family=Open+Sans:wght@400;600;700&display=swap" rel="stylesheet">
<style>
  :root {
    --navy: #1b2f6b;
    --ochre: #c75b12;
    --white: #ffffff;
    --backdrop: #e6e6e6;
  }
  * { margin: 0; padding: 0; box-sizing: border-box; }
  html, body {
    width: 1200px; height: 987px; overflow: hidden;
    background: var(--backdrop);
    font-family: "Open Sans", Arial, sans-serif;
  }
  .canvas { position: relative; width: 1200px; height: 987px; }

  .card {
    position: absolute; left: 293px; width: 615px; height: 352px;
    border-radius: 16px; overflow: hidden;
  }
  .card-front { top: 130px; background: var(--white); }
  .card-back { top: 505px; background: var(--navy); }

  .wordmark {
    position: absolute; left: 0; width: 100%;
    text-align: center; font-weight: 700; line-height: 1;
  }
  .card-front .wordmark { top: 78px; font-size: 84px; color: var(--navy); }
  .card-back .wordmark { top: 125px; font-size: 96px; color: var(--white); }

  .info-band {
    position: absolute; left: 0; top: 213px; width: 100%; height: 123px;
    background: var(--navy);
    border-top: 3px solid var(--ochre);
    border-bottom: 3px solid var(--ochre);
    box-shadow: inset 0 3px 0 var(--navy), inset 0 -3px 0 var(--navy);
    color: var(--white);
  }
  .info-band::before, .info-band::after {
    content: ""; position: absolute; left: 0; width: 100%; height: 2px; background: var(--navy);
  }
  .info-band::before { top: -6px; }
  .info-band::after { bottom: -6px; }

  .person {
    position: absolute; top: 13px; width: 100%; text-align: center;
    font-size: 20px; font-weight: 600; letter-spacing: 0.2px;
  }
  .person .role { font-size: 16px; font-weight: 400; }

  .contact-col {
    position: absolute; top: 55px; font-size: 16px; line-height: 23px;
  }
  .address { left: 32px; }
  .phones { left: 262px; }
  .web { left: 416px; }
  .divider {
    position: absolute; top: 58px; width: 2px; height: 42px; background: var(--white);
  }
  .divider-a { left: 241px; }
  .divider-b { left: 403px; }
  .phones .line { display: flex; align-items: center; gap: 8px; }
  .phones svg { width: 15px; height: 15px; fill: var(--white); }

  .back-url {
    position: absolute; top: 300px; width: 100%; text-align: center;
    color: var(--white); font-size: 16px; letter-spacing: 0.38em;
  }
</style>
</head>
<body>
<div class="canvas">
  <section class="card card-front">
    <div class="wordmark">R&amp;W</div>
    <div class="info-band">
      <div class="person">DANIEL REED - <span class="role">CEO/FOUNDER</span></div>
      <div class="contact-col address">4120 Cedarwood Lane<br>Fairbanks, Alaska 34712</div>
      <div class="divider divider-a"></div>
      <div class="contact-col phones">
        <div class="line">
          <svg viewBox="0 0 24 24" aria-hidden="true"><path d="M6.6 10.8a15.1 15.1 0 0 0 6.6 6.6l2.2-2.2a1 1 0 0 1 1-.25 11.4 11.4 0 0 0 3.6.57 1 1 0 0 1 1 1V20a1 1 0 0 1-1 1A17 17 0 0 1 3 4a1 1 0 0 1 1-1h3.5a1 1 0 0 1 1 1c0 1.25.2 2.45.57 3.57a1 1 0 0 1-.25 1z"/></svg>
          <span>571 208 4419</span>
        </div>
        <div class="line">
          <svg viewBox="0 0 24 24" aria-hidden="true"><path d="M7 2h8l2 2v5H7z M3 10h18v9H3z M6 20h12v2H6z"/></svg>
          <span>390 645 1127</span>
        </div>
      </div>
      <div class="divider divider-b"></div>
      <div class="contact-col web">hello@rwgroup.com<br>www.rwgroup.com</div>
    </div>
  </section>

  <section class="card card-back">
    <div class="wordmark">R&amp;W</div>
    <div class="back-url">www.rwgroup.com</div>
  </section>
</div>
</body>
</html>
```